Corvane Capital Business Cards

These are professional business cards that are for my family office.
Put fake emails and phone numbers as of now until I finalize those components. This family office controls my families investments, assets, and future. The cards should be professional.
..
.
.
.
I just uploaded another variation of a logo I would like to see as a business card to I am inbeteen which logo to use

Target Market(s)

business

Industry/Entity Type

business

Contact Information for Business Card

Professional, wealth related, finance related.

Requirements
Must have
• Logo

```html
<!DOCTYPE html>
<html lang="en">
<head>
<meta charset="utf-8">
<title>Corvane Capital Business Cards</title>
<link rel="stylesheet" href="https://fonts.googleapis.com/css2?family=Marcellus+SC&family=Lato:wght@400&display=swap">
<style>
  :root {
    --backdrop: #26272a;
    --backdrop-edge: #161719;
    --card: #171c2a;
    --card-edge: #10141e;
    --ink: #ffffff;
    --ink-soft: #d9dce3;
    --rule: #c9ccd3;
    --ghost: #1f2536;
  }
  * { margin: 0; padding: 0; box-sizing: border-box; }
  html, body { width: 1200px; height: 952px; overflow: hidden; }
  body {
    background: radial-gradient(ellipse at 55% 50%, var(--backdrop) 0%, var(--backdrop-edge) 100%);
    position: relative;
  }
  .card {
    position: absolute;
    width: 520px;
    height: 297px;
    background: var(--card);
    border-radius: 2px;
    box-shadow: 0 3px 0 var(--card-edge), 0 6px 0 var(--card-edge), 0 18px 40px rgba(0,0,0,.55);
    overflow: hidden;
  }
  .card--contact { left: 50px; top: 328px; }
  .card--brand { left: 630px; top: 328px; }

  /* brand side */
  .brand-rule {
    position: absolute;
    left: 0; right: 0; top: 132px;
    height: 1.5px;
    background: var(--rule);
  }
  .brand-mark {
    position: absolute;
    left: 312px; top: 62px;
    width: 110px; height: 110px;
    border: 2px solid var(--ink);
    border-radius: 50%;
    background: var(--card);
  }
  .brand-name {
    position: absolute;
    left: 118px; top: 150px;
    font-family: "Marcellus SC", serif;
    font-size: 22px;
    letter-spacing: 1px;
    color: var(--ink);
  }

  /* contact side */
  .holder {
    position: absolute;
    left: 30px; top: 28px;
  }
  .holder-name {
    font-family: "Marcellus SC", serif;
    font-size: 22px;
    letter-spacing: 1px;
    color: var(--ink);
  }
  .holder-title {
    font-family: "Lato", sans-serif;
    font-size: 11px;
    color: var(--ink-soft);
    margin-top: 2px;
  }
  .holder-underline {
    width: 32px; height: 1.5px;
    background: var(--ink);
    margin-top: 6px;
  }
  .contacts {
    position: absolute;
    left: 30px; top: 138px;
    list-style: none;
    font-family: "Lato", sans-serif;
    font-size: 11.5px;
    color: var(--ink);
  }
  .contacts li { display: flex; align-items: center; gap: 7px; height: 19px; }
  .contacts svg { width: 10px; height: 10px; fill: var(--ink); flex: none; }
  .ghost-ring {
    position: absolute;
    left: 300px; top: 150px;
    width: 260px; height: 260px;
    border: 4px solid var(--ghost);
    border-radius: 50%;
  }
</style>
</head>
<body>

<section class="card card--contact" aria-label="Contact side">
  <div class="ghost-ring" aria-hidden="true"></div>
  <div class="holder">
    <p class="holder-name">Daniel R. Hartwell</p>
    <p class="holder-title">Managing Director</p>
    <div class="holder-underline"></div>
  </div>
  <ul class="contacts">
    <li>
      <svg viewBox="0 0 10 10" aria-hidden="true"><path d="M2 0.5 L3.6 2.6 L2.8 3.6 Q3.8 5.8 6.2 7.2 L7.3 6.3 L9.5 8 L8.4 9.5 Q3.5 9 0.5 1.6 Z"/></svg>
      +00 123 456 78
    </li>
    <li>
      <svg viewBox="0 0 10 10" aria-hidden="true"><path d="M0.5 2 H9.5 V8.5 H0.5 Z M0.5 2 L5 5.6 L9.5 2" fill="none" stroke="#fff" stroke-width="1.2"/></svg>
      office@corvanecapital.com
    </li>
    <li>
      <svg viewBox="0 0 10 10" aria-hidden="true"><circle cx="5" cy="5" r="4.2" fill="none" stroke="#fff" stroke-width="1.2"/><path d="M0.8 5 H9.2 M5 0.8 Q2.5 5 5 9.2 M5 0.8 Q7.5 5 5 9.2" fill="none" stroke="#fff" stroke-width="0.8"/></svg>
      www.corvanecapital.com
    </li>
  </ul>
</section>

<section class="card card--brand" aria-label="Brand side">
  <div class="brand-rule"></div>
  <div class="brand-mark" aria-hidden="true"></div>
  <p class="brand-name">Corvane Capital</p>
</section>

</body>
</html>
```